Hybrid Seed corn and Soybean Sales business needs a website.

We here at "KW Grain" feel that we need a website to show a very professional side to our customer base. Although no actual ordering will take place on this website, we would like to put Plot and field trail data on the website. Along with a brief page for each of our hybrids and a place for customers to sign up for a newsletter. The company we sell hybrids for is MolvanGrain.com... Im not sure how this process works as far as myself updating the information or having the data actually put on the website, but feel free to contact me if you need the information. I will attach the logo for the company, (KW Grain).

Target Market(s)

Farmers, "Producers", Corn and soybean production

Industry/Entity Type

Business

Coding

Coded - Design and coding required

Number of Pages Required

5+ page

Colors
f78f20
ffffff

Requirements
Nice to have
• Similar layout to http://www.molvangrain.com/
• And it would be nice to incorporate our story into the website
• http://www.molvangrain.com/our-story/molvan-today/

```html
<!DOCTYPE html>
<html lang="en">
<head>
<meta charset="utf-8">
<title>KW Grain — Hybrid Seeds of Corn &amp; Soybean</title>
<link href="https://fonts.googleapis.com/css2?family=Open+Sans:wght@400;600;700&family=Oswald:wght@400&display=swap" rel="stylesheet">
<style>
:root{
  --orange:#f78f20;
  --orange-dark:#e07b10;
  --white:#ffffff;
  --ink:#1c1c1c;
  --body:#555555;
  --rule:#dddddd;
  --panel:#f3f3f3;
  --footer:#333333;
  --field-dark:#3e3a1c;
  --field-mid:#6f6a2a;
  --sky:#8a6a3a;
}
*{box-sizing:border-box;margin:0;padding:0}
html,body{width:821px;height:1200px;overflow:hidden}
body{position:relative;background:var(--white);font-family:"Open Sans",Arial,sans-serif;color:var(--body)}
.abs{position:absolute}

.topbar{left:0;top:0;width:821px;height:23px;background:var(--orange)}
.topbar-tagline{left:34px;top:5px;font-size:8.5px;color:var(--white)}
.search{left:655px;top:3px;width:128px;height:17px;background:var(--white);border-radius:3px;font-size:8px;color:#777;padding:3px 6px}
.search svg{position:absolute;right:6px;top:3px}

.header{left:0;top:23px;width:821px;height:56px;background:var(--white)}
.brand{left:35px;top:37px;display:flex;align-items:center;gap:6px;font-size:17px;font-weight:700;color:var(--orange)}
.brand-mark{width:12px;height:12px;background:var(--orange);border-radius:50%}
.nav{top:46px;font-size:8.5px;color:var(--ink);letter-spacing:.2px}
.nav.active{color:var(--orange)}

.hero{left:0;top:79px;width:821px;height:360px;background:linear-gradient(180deg,var(--sky) 0%,#6b5a30 18%,var(--field-dark) 30%,var(--field-mid) 60%,#4c4720 100%)}
.hero-photo{left:152px;top:157px;width:206px;height:206px;border-radius:50%;background:radial-gradient(circle,#d8c49a 0%,#b27a4a 55%,#8a6030 100%);border:5px solid #8a6a2c}
.hero-title{left:381px;top:180px;width:265px;font-family:"Oswald",sans-serif;font-size:15px;line-height:20px;color:var(--white);text-transform:uppercase}
.hero-text{left:381px;top:226px;width:290px;font-size:9.5px;line-height:18px;color:var(--white)}
.btn-hero{left:383px;top:291px;width:146px;height:39px;background:var(--orange);color:var(--white);font-size:11.5px;display:flex;align-items:center;justify-content:center;border-radius:2px}
.hero-shadow{left:180px;top:439px;width:460px;height:22px;background:radial-gradient(ellipse at 50% 0%,rgba(0,0,0,.18),rgba(0,0,0,0) 70%)}

.welcome-title{left:0;top:470px;width:821px;text-align:center;font-size:20px;font-weight:600;color:var(--ink)}
.welcome-sub{left:0;top:497px;width:821px;text-align:center;font-size:20px;font-weight:600;color:var(--orange)}
.welcome-text{left:68px;top:542px;width:685px;text-align:center;font-size:7.7px;line-height:15.5px}
.welcome-rule{left:224px;top:601px;width:372px;height:1px;background:var(--rule)}

.card{top:637px;width:175px;height:128px;background:var(--white);border:1px solid #e2e2e2;box-shadow:0 0 3px rgba(0,0,0,.12);padding:3px}
.card-photo{width:167px;height:96px}
.card-label{width:167px;height:26px;background:var(--orange);color:var(--white);font-size:11.5px;font-weight:600;padding:5px 12px}

.panel{left:0;top:805px;width:821px;height:226px;background:var(--panel);border-top:1px solid #e4e4e4;border-bottom:1px solid #e4e4e4}
.panel-title{top:821px;font-size:15.5px;font-weight:700;color:var(--ink)}
.video{left:35px;top:864px;width:200px;height:132px;background:#111;border:2px solid #111}
.video-frame{width:196px;height:107px;background:linear-gradient(180deg,#3a1d08 0%,#a2480c 55%,#f0a020 85%,#5a2a08 100%)}
.video-bar{left:6px;top:116px;width:178px;height:3px;background:#555}
.video-progress{left:6px;top:116px;width:24px;height:3px;background:#3a7bd5}
.video-knob{left:27px;top:113px;width:8px;height:8px;border-radius:50%;background:var(--white)}
.about-text{left:251px;top:866px;width:215px;font-size:7.8px;line-height:15.5px}
.about-item{left:251px;width:196px;height:24px;border-bottom:1px solid var(--rule);font-size:7.8px;padding-left:16px;line-height:17px}
.about-item svg{position:absolute;left:0;top:6px}
.news-text{left:564px;top:858px;width:180px;font-size:7.8px;line-height:16px}
.news-input{left:564px;top:899px;width:177px;height:22px;background:var(--white);border:1px solid #ccc;font-size:7.8px;color:#999;padding:4px 8px}
.btn-news{left:564px;top:931px;width:100px;height:24px;background:var(--orange);border-radius:2px;color:var(--white);font-size:7.5px;font-weight:700;display:flex;align-items:center;justify-content:center}

.partner{top:1064px;display:flex;align-items:center;gap:7px;font-size:14px;font-weight:700;color:var(--ink)}
.partner-mark{width:12px;height:12px;background:var(--orange)}

.footer{left:0;top:1119px;width:821px;height:81px;background:var(--footer)}
.footer-shadow{left:130px;top:1119px;width:560px;height:18px;background:radial-gradient(ellipse at 50% 0%,rgba(0,0,0,.45),rgba(0,0,0,0) 70%)}
.copyright{left:0;top:1153px;width:821px;text-align:center;font-size:8.5px;color:var(--white)}
</style>
</head>
<body>

<div class="abs topbar"></div>
<div class="abs topbar-tagline">We sell hybrid seeds of Corn &amp; Soybean.</div>
<div class="abs search">search
  <svg width="11" height="11" viewBox="0 0 11 11"><circle cx="4.5" cy="4.5" r="3.3" fill="none" stroke="#333" stroke-width="1.4"/><line x1="7" y1="7" x2="10.3" y2="10.3" stroke="#333" stroke-width="1.8"/></svg>
</div>

<div class="abs header"></div>
<div class="abs brand"><span class="brand-mark"></span>KW Grain</div>
<div class="abs nav active" style="left:508px">HOME</div>
<div class="abs nav" style="left:556px">PRODUCTS</div>
<div class="abs nav" style="left:622px">ABOUT US</div>
<div class="abs nav" style="left:686px">BLOG</div>
<div class="abs nav" style="left:730px">CONTACT US</div>

<div class="abs hero" role="img" aria-label="Golden soybean field at sunset with a row of trees on the horizon"></div>
<div class="abs hero-photo" role="img" aria-label="Bowl of mixed beans and soybeans"></div>
<div class="abs hero-title">Lorem ipsum is simply dummy text of the printing</div>
<div class="abs hero-text">Duis sed odio sit amet nibh vulputate cursus a sit amet mauris. Morbi accumsan ipsum velit. Nam nec tellus a odio tincidunt auctor a ornare odio.</div>
<div class="abs btn-hero">VIEW NOW</div>
<div class="abs hero-shadow"></div>

<div class="abs welcome-title">Welcome To&nbsp; KW Grain</div>
<div class="abs welcome-sub">We sell hybrid seeds of Corn &amp; Soybean</div>
<p class="abs welcome-text">Proin gravida nibh vel velit auctor aliquet. Aenean sollicitudin, lorem quis bibendum auctor, nisi elit consequat ipsum, nec sagittis sem nibh id elit. Duis sed odio sit amet nibh vulputate cursus a sit amet mauris. Morbi accumsan ipsum velit. Nam nec tellus a odio tincidunt auctor a ornare odio. Sed non mauris vitae erat consequat auctor eu in elit. Class aptent taciti sociosqu ad litora torquent per conubia nostra, per inceptos himenaeos.</p>
<div class="abs welcome-rule"></div>

<div class="abs card" style="left:33px">
  <div class="card-photo" role="img" aria-label="Hands holding corn kernels" style="background:linear-gradient(160deg,#4a2a12,#c8901e 60%,#e8a83a)"></div>
  <div class="card-label">Hybrid Seeds</div>
</div>
<div class="abs card" style="left:225px">
  <div class="card-photo" role="img" aria-label="Combine unloading grain into a trailer" style="background:linear-gradient(180deg,#7fa8d0 0%,#b8c4c8 35%,#a03828 60%,#c8902a 100%)"></div>
  <div class="card-label">Hybrid Seeds</div>
</div>
<div class="abs card" style="left:417px">
  <div class="card-photo" role="img" aria-label="Hands holding soybeans over planted rows" style="background:linear-gradient(180deg,#3a3530 0%,#5a5040 50%,#c8a878 100%)"></div>
  <div class="card-label">Hybrid Seeds</div>
</div>
<div class="abs card" style="left:610px">
  <div class="card-photo" role="img" aria-label="Hand holding an ear of corn in the field" style="background:linear-gradient(160deg,#2e3a1a,#6a6a22 45%,#d8a020 75%,#4a3a1a)"></div>
  <div class="card-label">Hybrid Seeds</div>
</div>

<div class="abs panel"></div>
<div class="abs panel-title" style="left:35px">About us</div>
<div class="abs video">
  <div class="video-frame" role="img" aria-label="Video still of a sunset over a field"></div>
  <div class="abs video-bar"></div>
  <div class="abs video-progress"></div>
  <div class="abs video-knob"></div>
  <svg class="abs" style="left:186px;top:112px" width="8" height="10" viewBox="0 0 8 10"><rect x="0" y="0" width="3" height="10" fill="#fff"/><rect x="5" y="0" width="3" height="10" fill="#fff"/></svg>
</div>
<p class="abs about-text">Proin gravida nibh vel velit auctor aliquet. Aenean sollicitudin, lorem quis bibendum auctor, nisi elit consequat ipsum, nec sagittis sem nibh id elit.</p>
<div class="abs about-item" style="top:926px"><svg width="7" height="5" viewBox="0 0 7 5"><path d="M0 2.5H6M4 .5L6 2.5L4 4.5" stroke="#6aa84f" fill="none"/></svg>Aenean sollicitudin, lorem quis bibendum auctor</div>
<div class="abs about-item" style="top:950px"><svg width="7" height="5" viewBox="0 0 7 5"><path d="M0 2.5H6M4 .5L6 2.5L4 4.5" stroke="#6aa84f" fill="none"/></svg>Aenean sollicitudin, lorem quis bibendum auctor</div>
<div class="abs about-item" style="top:974px"><svg width="7" height="5" viewBox="0 0 7 5"><path d="M0 2.5H6M4 .5L6 2.5L4 4.5" stroke="#6aa84f" fill="none"/></svg>Aenean sollicitudin, lorem quis bibendum auctor</div>

<div class="abs panel-title" style="left:562px">Newsletter</div>
<p class="abs news-text">For details of multi-user licencesemail hello@kwgrainfarm.net</p>
<div class="abs news-input">Enter your email id :</div>
<div class="abs btn-news">SUBSCRIBE TODAY</div>

<div class="abs partner" style="left:112px"><span class="partner-mark"></span>Ridgeline AgroSciences</div>
<div class="abs partner" style="left:410px"><span class="partner-mark"></span>Fieldguard</div>
<div class="abs partner" style="left:604px"><span class="partner-mark"></span>Molvan</div>

<div class="abs footer"></div>
<div class="abs footer-shadow"></div>
<div class="abs copyright">©2015 KW Grain. All Rights Reserved.&nbsp; Terms &amp; Conditions Privacy Policy</div>

</body>
</html>
```